indépendant en tant que Massothérapeute et Préparateur Mental, j'ai besoin de ...

Massothérapeute et préparateur mental indépendant, je recherche une carte de visite sobre et dynamique, sans images liées au massage ou à la préparation mentale mais intégrant mon logo. Les couleurs que j'aime bien sont : Blanc, gris, anthracite, noir et jaune

Contact Information for Business Card

carte de préférence Horizontale
neutre qui puisse toucher le deux domaines Massothérapie et préparation mentale

Requirements
Must have
• mon projet doit intégrer au recto:
LOGO
Loïc Bardèze
078 513 26 48
info@loicbardeze.ch
et éventuellement www.loicbardeze.ch

et au verso les deux adresses:

Chemin des Ormilles 7B
1400 Yverdon-les-Bains

Route de la Gravière 9
1700 Fribourg

Should not have
• mon projet ne doit pas contenir d'image en liens avec le massage ni la préparation mentale.

```html
<!DOCTYPE html>
<html lang="fr">
<head>
<meta charset="utf-8">
<title>Loïc Bardèze – Cartes de visite</title>
<link href="https://fonts.googleapis.com/css2?family=Arimo:wght@400;700&display=swap" rel="stylesheet">
<style>
  :root {
    --bg: #2b2b2b;
    --card: #f6f6f6;
    --card-shade: #ececec;
    --ink: #1e1e1e;
    --ink-soft: #3a3a3a;
  }
  * { margin: 0; padding: 0; box-sizing: border-box; }
  html, body { width: 1200px; height: 1015px; overflow: hidden; }
  body {
    background: var(--bg);
    font-family: "Arimo", Arial, sans-serif;
    color: var(--ink);
    display: flex;
    flex-direction: column;
    align-items: center;
    justify-content: center;
    gap: 60px;
  }
  .card {
    position: relative;
    width: 760px;
    height: 420px;
    background: var(--card);
    box-shadow: 0 10px 30px rgba(0,0,0,.45);
    overflow: hidden;
  }
  .card__texture {
    position: absolute; inset: 0;
    background: linear-gradient(135deg, var(--card) 0%, var(--card-shade) 100%);
  }
  .logo {
    position: absolute;
    display: flex;
    align-items: center;
    gap: 14px;
  }
  .logo__mark {
    background: var(--ink);
    flex: none;
  }
  .logo__name {
    font-weight: 700;
    letter-spacing: .5px;
    line-height: 1;
    color: var(--ink);
  }
  .logo__tagline {
    font-weight: 400;
    text-transform: uppercase;
    letter-spacing: 1px;
    color: var(--ink-soft);
    margin-top: 5px;
  }
  /* Front */
  .card--front .logo { left: 190px; top: 290px; }
  .card--front .logo__mark { width: 26px; height: 26px; }
  .card--front .logo__name { font-size: 30px; }
  .card--front .logo__tagline { font-size: 11px; }
  /* Back */
  .card--back .logo { left: 60px; top: 58px; }
  .card--back .logo__mark { width: 50px; height: 50px; }
  .card--back .logo__name { font-size: 34px; }
  .card--back .logo__tagline { font-size: 12px; }
  .details {
    position: absolute;
    left: 340px;
    top: 150px;
    font-size: 19px;
    line-height: 1.2;
    color: var(--ink-soft);
  }
  .details__name {
    font-size: 26px;
    font-weight: 700;
    color: var(--ink);
    margin-bottom: 14px;
    letter-spacing: .5px;
  }
  .contact { list-style: none; margin-bottom: 12px; }
  .contact li { display: flex; align-items: center; gap: 8px; }
  .contact svg { width: 15px; height: 15px; fill: var(--ink); flex: none; }
  .address { margin-top: 6px; }
</style>
</head>
<body>
  <section class="card card--front">
    <div class="card__texture" role="img" aria-label="Motif gaufré blanc répétant le monogramme"></div>
    <div class="logo">
      <span class="logo__mark"></span>
      <div>
        <div class="logo__name">Loïc Bardèze</div>
        <div class="logo__tagline">Massothérapeute / Préparateur Mental</div>
      </div>
    </div>
  </section>

  <section class="card card--back">
    <div class="card__texture" role="img" aria-label="Motif gaufré blanc répétant le monogramme"></div>
    <div class="logo">
      <span class="logo__mark"></span>
      <div>
        <div class="logo__name">Loïc Bardèze</div>
        <div class="logo__tagline">Massothérapeute / Préparateur Mental</div>
      </div>
    </div>
    <div class="details">
      <div class="details__name">LOÏC BARDÈZE</div>
      <ul class="contact">
        <li>
          <svg viewBox="0 0 16 16" aria-hidden="true"><path d="M3.5 1l2.5 3-1.5 1.6a8 8 0 0 0 5.9 5.9L12 10l3 2.5-1.4 2.2C7.8 15.2.8 8.2 1.3 2.4z"/></svg>
          078 513 26 48
        </li>
        <li>
          <svg viewBox="0 0 16 16" aria-hidden="true"><path d="M1 3h14v10H1zM2 4.2v.4l6 4 6-4v-.4z"/></svg>
          info@loicbardeze.ch
        </li>
        <li>
          <svg viewBox="0 0 16 16" aria-hidden="true"><path d="M8 1a7 7 0 1 0 0 14A7 7 0 0 0 8 1zm0 1.3c.8 0 1.7 1.6 2 4.1H6c.3-2.5 1.2-4.1 2-4.1zM2.4 7.4h2.5c0 .4 0 .8 0 1.2H2.4a5.6 5.6 0 0 1 0-1.2zm3.6 0h4a11 11 0 0 1 0 1.2H6a11 11 0 0 1 0-1.2zm5.1 0h2.5a5.6 5.6 0 0 1 0 1.2h-2.5zM6 9.6h4c-.3 2.5-1.2 4.1-2 4.1s-1.7-1.6-2-4.1z"/></svg>
          www.loicbardeze.ch
        </li>
      </ul>
      <p class="address">Chemin des Ormilles 7B<br>1400 Yverdon-les-Bains</p>
      <p class="address">Route de la Gravière 9<br>1700 Freiburg</p>
    </div>
  </section>
</body>
</html>
```